Heron Loan Partners Business Card

We need a business card design for our mortgage servicing company. In addition to servicing the loans of homeowners, we help homeowners with purchasing their homes and any mortgage refinancing. We would like to see designs that use the colors in the logo attached below (gold-ish yellow and navy blue), and any other design you deem fit! The design should communicate a simpler life with smart mortgages provided by Heron.

```html
<!DOCTYPE html>
<html lang="en">
<head>
<meta charset="utf-8">
<title>Heron Loan Partners Business Card</title>
<link href="https://fonts.googleapis.com/css2?family=Montserrat:wght@500;700;800&display=swap" rel="stylesheet">
<style>
  :root {
    --navy: #262152;
    --gold: #e2ae35;
    --white: #ffffff;
    --ink: #1d1b33;
    --backdrop: #e9e9ec;
  }
  * { box-sizing: border-box; margin: 0; padding: 0; }
  html, body { width: 1200px; height: 880px; overflow: hidden; }
  body {
    background: var(--backdrop);
    font-family: "Montserrat", sans-serif;
    display: flex; flex-direction: column; align-items: center; justify-content: center;
    gap: 40px;
  }
  .card {
    position: relative;
    width: 700px; height: 400px;
    overflow: hidden;
    box-shadow: 0 6px 18px rgba(0,0,0,0.18);
  }
  .card-back { background: var(--navy); display: flex; align-items: center; justify-content: center; }
  .brand-name { font-weight: 800; color: var(--gold); letter-spacing: 0.5px; line-height: 1; }
  .card-back .brand-name { font-size: 50px; }
  .card-front { background: var(--white); }
  .card-front .brand-name { position: absolute; top: 60px; left: 330px; font-size: 28px; }
  .wave { position: absolute; inset: 0; width: 100%; height: 100%; }
  .holder { position: absolute; top: 160px; left: 0; }
  .holder-bar { position: absolute; left: 22px; top: 2px; width: 16px; height: 50px; background: var(--gold); }
  .holder-name { margin-left: 52px; font-size: 20px; font-weight: 800; color: var(--navy); letter-spacing: 0.3px; }
  .holder-name .surname { color: var(--gold); }
  .holder-role { margin-left: 52px; margin-top: 4px; font-size: 17px; font-weight: 500; color: var(--ink); }
  .contacts { position: absolute; left: 60px; top: 240px; list-style: none; }
  .contacts li {
    display: flex; align-items: center; gap: 12px;
    font-size: 17px; font-weight: 500; color: var(--ink); height: 28px;
  }
  .contacts svg { width: 18px; height: 18px; fill: var(--gold); flex: none; }
  .address {
    position: absolute; right: 40px; top: 108px;
    text-align: right; font-size: 17px; font-weight: 500; color: var(--ink); line-height: 1.45;
  }
</style>
</head>
<body>
  <section class="card card-back">
    <div class="brand-name">Heron Loan Partners</div>
  </section>

  <section class="card card-front">
    <svg class="wave" viewBox="0 0 700 400" preserveAspectRatio="none" aria-hidden="true">
      <path d="M0 390 C 180 387, 300 362, 400 305 S 600 205 700 192 L700 400 L0 400 Z" fill="var(--navy)"/>
      <path d="M0 376 C 180 373, 295 348, 392 292 S 600 190 700 177" fill="none" stroke="var(--gold)" stroke-width="5"/>
    </svg>

    <div class="brand-name">Heron Loan Partners</div>

    <div class="holder">
      <span class="holder-bar"></span>
      <p class="holder-name">DANA <span class="surname">WELLFORD</span></p>
      <p class="holder-role">Owner</p>
    </div>

    <ul class="contacts">
      <li>
        <svg viewBox="0 0 24 24"><path d="M6.6 10.8a15.1 15.1 0 0 0 6.6 6.6l2.2-2.2c.3-.3.7-.4 1-.2 1.1.4 2.3.6 3.6.6.6 0 1 .4 1 1V20c0 .6-.4 1-1 1A17 17 0 0 1 3 4c0-.6.4-1 1-1h3.5c.6 0 1 .4 1 1 0 1.3.2 2.5.6 3.6.1.3 0 .7-.2 1z"/></svg>
        555.014.2290
      </li>
      <li>
        <svg viewBox="0 0 24 24"><path d="M2 5h20v14H2z"/><path d="M3 6.5 12 13l9-6.5" fill="none" stroke="#fff" stroke-width="1.5"/></svg>
        info@heronloanpartners.com
      </li>
      <li>
        <svg viewBox="0 0 24 24"><circle cx="12" cy="12" r="10"/><path d="M2 12h20M12 2c3 3 3 17 0 20M12 2c-3 3-3 17 0 20" fill="none" stroke="#fff" stroke-width="1.4"/></svg>
        www.heronloanpartners.com
      </li>
    </ul>

    <p class="address">2450 Alder Park Ave, Ste<br>100, Fairview, TX 75000</p>
  </section>
</body>
</html>
```